Stonebridge Building and Projects business cards

A business card with watermark background (construction work)

Company logo attached

Home improvement projects
House renovations
Bathroom and kitchen renovations
House extensions
New builds and granny flats

Director Omar Haddani
(Phone number)
omar@sbpbuilding.com.au
(Instagram logo) sbp_building

```html
<!DOCTYPE html>
<html lang="en">
<head>
<meta charset="utf-8">
<title>Stonebridge Building and Projects – Business Cards</title>
<link href="https://fonts.googleapis.com/css2?family=Roboto:wght@400;500;700&display=swap" rel="stylesheet">
<style>
  :root {
    --brand-blue: #1673bd;
    --ink: #2b2b2b;
    --ink-soft: #555a60;
    --card-white: #fbfbfb;
    --watermark: #eceded;
    --stage: #e6e7e9;
    --band-text: #ffffff;
  }
  * { box-sizing: border-box; margin: 0; padding: 0; }
  html, body { width: 1200px; height: 1050px; overflow: hidden; }
  body {
    background: var(--stage);
    font-family: "Roboto", Arial, sans-serif;
    position: relative;
  }
  .card {
    position: absolute;
    width: 560px;
    height: 340px;
    background: var(--card-white);
    border-radius: 22px;
    box-shadow: 0 6px 18px rgba(0,0,0,.12);
    overflow: hidden;
  }
  .card--front { left: 70px; top: 150px; }
  .card--back  { left: 570px; top: 560px; }

  /* Wordmark */
  .wordmark {
    display: flex;
    align-items: center;
    gap: 10px;
    color: var(--brand-blue);
    font-weight: 700;
    line-height: 1.05;
  }
  .wordmark__square {
    width: 14px; height: 14px;
    background: var(--brand-blue);
    flex: none;
  }
  .tagline {
    color: var(--brand-blue);
    font-weight: 500;
    font-style: normal;
  }

  /* Front */
  .front__watermark {
    position: absolute; left: 40px; top: 20px;
    width: 300px; height: 190px;
    background: linear-gradient(135deg, var(--watermark), rgba(236,237,237,0));
    border-radius: 8px;
  }
  .front__brand {
    position: absolute; left: 0; right: 0; top: 52px;
    text-align: center;
    display: flex; flex-direction: column; align-items: center; gap: 8px;
  }
  .front__brand .wordmark { font-size: 30px; }
  .front__brand .tagline { font-size: 20px; border-top: 2px solid var(--brand-blue); padding-top: 4px; }
  .services-band {
    position: absolute; left: 0; right: 0; top: 176px;
    height: 88px;
    background: var(--brand-blue);
    color: var(--band-text);
    display: flex; flex-direction: column; justify-content: center; align-items: center;
    gap: 6px;
    font-size: 16px;
  }
  .services-band span + span::before { content: "|"; margin: 0 8px; opacity: .85; }
  .front__links {
    position: absolute; left: 0; right: 0; top: 284px;
    display: flex; justify-content: center; gap: 34px;
    font-size: 15px; color: var(--ink-soft);
  }
  .link { display: flex; align-items: center; gap: 8px; }
  .icon { width: 16px; height: 16px; flex: none; }
  .icon-dot { width: 14px; height: 14px; border-radius: 50%; background: var(--brand-blue); flex: none; }

  /* Back */
  .back__brand {
    position: absolute; left: 34px; top: 44px;
    display: flex; flex-direction: column; gap: 6px;
  }
  .back__brand .wordmark { font-size: 22px; max-width: 260px; }
  .back__brand .tagline { font-size: 15px; padding-left: 24px; }
  .back__decor {
    position: absolute; right: 0; top: 0;
    width: 230px; height: 340px;
    background: linear-gradient(160deg, var(--brand-blue) 0%, #5c95c6 45%, #cfd3d6 100%);
    clip-path: polygon(28% 0, 100% 0, 100% 100%, 0 100%);
  }
  .person {
    position: absolute; left: 40px; top: 150px;
  }
  .person__name { color: var(--brand-blue); font-size: 22px; font-weight: 700; }
  .person__role { color: var(--ink-soft); font-size: 15px; margin-top: 2px; }
  .contacts {
    position: absolute; left: 40px; top: 220px;
    list-style: none;
    display: flex; flex-direction: column; gap: 6px;
    font-size: 15px; color: var(--ink);
  }
  .contacts li { display: flex; align-items: center; gap: 10px; }
</style>
</head>
<body>

<section class="card card--front" aria-label="Business card front">
  <div class="front__watermark" role="img" aria-label="Faint construction watermark"></div>
  <div class="front__brand">
    <div class="wordmark"><span class="wordmark__square"></span>Stonebridge Building and Projects</div>
    <div class="tagline">Built to last!</div>
  </div>
  <div class="services-band">
    <div><span>Home Improvement Projects</span><span>House Renovations</span><span>House Extensions</span></div>
    <div><span>Bathroom &amp; Kitchen Renovations</span><span>New Builds &amp; Granny Flats</span></div>
  </div>
  <div class="front__links">
    <div class="link"><span class="icon-dot"></span>sbp_building</div>
    <div class="link">
      <svg class="icon" viewBox="0 0 16 16" fill="none" stroke="#1673bd" stroke-width="1.4"><circle cx="8" cy="8" r="6.5"/><ellipse cx="8" cy="8" rx="2.8" ry="6.5"/><path d="M1.5 8h13"/></svg>
      sbpbuilding.com.au
    </div>
  </div>
</section>

<section class="card card--back" aria-label="Business card back">
  <div class="back__decor" role="img" aria-label="Large decorative construction pattern"></div>
  <div class="back__brand">
    <div class="wordmark"><span class="wordmark__square"></span>Stonebridge Building and Projects</div>
    <div class="tagline">Built to last!</div>
  </div>
  <div class="person">
    <div class="person__name">Omar Haddani</div>
    <div class="person__role">Managing Director</div>
  </div>
  <ul class="contacts">
    <li>
      <svg class="icon" viewBox="0 0 16 16" fill="none" stroke="#1673bd" stroke-width="1.4"><path d="M4 2l2.2 2.5-1.3 1.6a8 8 0 0 0 5 5l1.6-1.3L14 12l-1.4 1.8C7 13.5 2.5 9 2.2 3.4z"/></svg>
      0400 318 762
    </li>
    <li>
      <svg class="icon" viewBox="0 0 16 16" fill="none" stroke="#1673bd" stroke-width="1.4"><rect x="1.5" y="3.5" width="13" height="9"/><path d="M1.5 3.5 8 9l6.5-5.5"/></svg>
      omar@sbpbuilding.com.au
    </li>
    <li>
      <svg class="icon" viewBox="0 0 16 16" fill="none" stroke="#1673bd" stroke-width="1.4"><circle cx="8" cy="8" r="6.5"/><ellipse cx="8" cy="8" rx="2.8" ry="6.5"/><path d="M1.5 8h13"/></svg>
      sbpbuilding.com.au
    </li>
    <li><span class="icon-dot"></span>sbp_building</li>
  </ul>
</section>

</body>
</html>
```